Business card

I have changed logo's and colors. I have uploaded the new logo and colors.

In my head I am thinking about the main logo and text beside logo to be on one side of the card. The other side of the card to have just my picture and contact information.

The "R" emblem and the "equal housing" emblem... cut he MLS from the "R". and remove the wording from the house emblem.

Info on Card:

Lyle Penrose
Designated Broker, CDPE, CNE, GRI
Direct: 602.555.0143
Fax: 623.555.0187
Lyle@PenroseandAssociates.example
www.PenroseandAssociates.example
4153 West Marlow Lane Glendale, AZ 85391

Please see brief as I have uploaded a new logo and a few notes.

Reason: I changed the logo and colors. Please see brief

I am leaning towards maybe a black business card(or at least on the front where the logo is). I liked several designs that were submitted. Please re-submit.

```html
<!DOCTYPE html>
<html lang="en">
<head>
<meta charset="utf-8">
<title>Penrose &amp; Associates — Business Card</title>
<link rel="stylesheet" href="https://fonts.googleapis.com/css2?family=Cinzel:wght@400;600&family=Open+Sans:wght@400;600&display=swap">
<style>
  :root {
    --page-bg: #d9dadb;
    --card-light: #8e8f91;
    --card-mid: #727375;
    --card-dark: #505153;
    --card-deep: #3d3e40;
    --panel: #a3a4a6;
    --panel-edge: rgba(255,255,255,0.35);
    --band-top: #b4b5b7;
    --band-bottom: #8d8e90;
    --ink-white: #ffffff;
    --ink-soft: #ececec;
    --rule: rgba(255,255,255,0.55);
    --badge-ring: #d8d9da;
    --badge-gold: #e3a21a;
    --badge-blue: #2d5bb0;
    --badge-red: #c9252b;
    --badge-green: #2f9a45;
  }
  * { box-sizing: border-box; margin: 0; padding: 0; }
  html, body { width: 1200px; height: 840px; overflow: hidden; }
  body { background: var(--page-bg); position: relative; font-family: "Open Sans", sans-serif; }

  .card {
    position: absolute; top: 132px; width: 330px; height: 576px;
    overflow: hidden; box-shadow: 0 6px 18px rgba(0,0,0,0.25);
  }

  /* Front side */
  .card-front {
    left: 210px;
    background: linear-gradient(180deg, var(--card-light) 0%, var(--card-mid) 55%, var(--card-dark) 100%);
  }
  .logo-panel {
    position: absolute; left: 96px; top: 0; width: 138px; height: 190px;
    background: var(--panel); border-bottom: 2px solid var(--panel-edge);
    display: flex; align-items: flex-start; justify-content: center; gap: 7px; padding-top: 60px;
  }
  .logo-dot { width: 24px; height: 24px; border-radius: 50%; background: var(--ink-white); flex: none; }
  .logo-name {
    font-family: "Cinzel", serif; color: var(--ink-white);
    font-size: 12.5px; line-height: 1.2; letter-spacing: 0.4px;
  }
  .agent { position: absolute; left: 70px; top: 218px; color: var(--ink-white); }
  .agent-name { font-family: "Cinzel", serif; font-size: 27px; letter-spacing: 0.5px; line-height: 1.1; }
  .agent-title { font-family: "Cinzel", serif; font-size: 14px; margin-top: 6px; color: var(--ink-soft); }
  .agent-creds { font-family: "Cinzel", serif; font-size: 10px; color: var(--ink-soft); }
  .contact { position: absolute; left: 46px; top: 306px; width: 270px; color: var(--ink-white); font-size: 11.5px; line-height: 1.55; }
  .contact-row { display: flex; gap: 8px; align-items: flex-start; }
  .contact-row svg { flex: none; margin-top: 3px; }
  .contact-rule { height: 1px; background: var(--rule); margin: 3px 0 6px 24px; width: 175px; }
  .badge-band {
    position: absolute; left: 0; top: 436px; width: 100%; height: 92px;
    background: linear-gradient(180deg, var(--band-top), var(--band-bottom));
    display: flex; justify-content: center; align-items: center; gap: 18px;
  }
  .badge { width: 46px; height: 46px; border-radius: 50%; border: 3px solid var(--badge-ring); }
  .badge--gold { background: var(--badge-gold); }
  .badge--blue { background: var(--badge-blue); }
  .badge--red { background: var(--badge-red); }
  .badge--green { background: var(--badge-green); }
  .web-band {
    position: absolute; left: 0; top: 528px; width: 100%; height: 48px;
    background: var(--card-deep); color: var(--ink-white);
    display: flex; align-items: center; justify-content: center; font-size: 11.5px; font-weight: 600;
  }

  /* Back side */
  .card-back {
    left: 660px;
    background: linear-gradient(180deg, var(--card-mid) 0%, var(--card-dark) 100%);
    display: flex; align-items: flex-start; justify-content: center; gap: 12px; padding-top: 120px;
  }
  .back-dot { width: 44px; height: 44px; border-radius: 50%; background: var(--ink-white); flex: none; }
  .back-name { font-family: "Cinzel", serif; color: var(--ink-white); font-size: 22px; line-height: 1.15; letter-spacing: 1.5px; }
</style>
</head>
<body>

<section class="card card-front" aria-label="Card front">
  <div class="logo-panel">
    <span class="logo-dot"></span>
    <span class="logo-name">Penrose<br>&amp; Associates</span>
  </div>

  <div class="agent">
    <div class="agent-name">Lyle Penrose</div>
    <div class="agent-title">Designated Broker</div>
    <div class="agent-creds">CDPE, CNE, GRI</div>
  </div>

  <div class="contact">
    <div class="contact-row">
      <svg width="16" height="16" viewBox="0 0 16 16" fill="none" stroke="#fff" stroke-width="1.2"><circle cx="8" cy="8" r="6.5"/><ellipse cx="8" cy="8" rx="3" ry="6.5"/><path d="M1.5 8h13M2.5 4.8h11M2.5 11.2h11"/></svg>
      <span>4153 West Marlow Lane Glendale<br>AZ 85391</span>
    </div>
    <div class="contact-rule"></div>
    <div class="contact-row">
      <svg width="16" height="12" viewBox="0 0 16 12"><rect x="0.5" y="0.5" width="15" height="11" fill="#fff"/><path d="M0.5 0.5l7.5 6 7.5-6" fill="none" stroke="#6f7072" stroke-width="1"/></svg>
      <span>Lyle@PenroseandAssociates.example</span>
    </div>
    <div class="contact-row">
      <svg width="16" height="14" viewBox="0 0 16 14" fill="#fff"><path d="M1 4c0-2 3-3 7-3s7 1 7 3v1h-3.5V3.5h-7V5H1z"/><rect x="3" y="6" width="10" height="7" rx="1"/></svg>
      <span>602.555.0143</span>
    </div>
  </div>

  <div class="badge-band">
    <span class="badge badge--gold"></span>
    <span class="badge badge--blue"></span>
    <span class="badge badge--red"></span>
    <span class="badge badge--green"></span>
  </div>

  <div class="web-band">www.PenroseandAssociates.example</div>
</section>

<section class="card card-back" aria-label="Card back">
  <span class="back-dot"></span>
  <span class="back-name">Penrose<br>&amp; Associates</span>
</section>

</body>
</html>
```